Kellwyn Surface Records

I have a current web site that it looking quite aged and it needs a new lease of life. This is a Graffiti Management Website so is all about data processing and management of information. I want a html 5 view on any platform design. clean crisp and new. I have provided some screen shots of my current site.

Target Market(s)

The Target Market will be local government. most users will not be heavy pc users

Industry/Entity Type

Management

Font styles to use
Sans Serif
Other font styles liked:
• web font like calibri

Colors

Designer to choose colors to be used in the design.

Requirements
Must have
• Must have menus similar to attachments

```html
<!DOCTYPE html>
<html lang="en">
<head>
<meta charset="utf-8">
<title>KSR – Kellwyn Surface Records</title>
<link rel="stylesheet" href="https://fonts.googleapis.com/css2?family=Open+Sans:wght@400;600;700&display=swap">
<style>
  :root {
    --green: #8cc63f;
    --green-dark: #5a8f1a;
    --ink: #231f20;
    --header-bg: #ebebea;
    --rule: #2a2a2a;
    --section-bg: #dcdcd9;
    --footer-bg: #0d0d0d;
    --white: #ffffff;
  }
  * { margin: 0; padding: 0; box-sizing: border-box; }
  html, body { width: 1200px; height: 651px; overflow: hidden; }
  body { font-family: "Open Sans", Arial, sans-serif; color: var(--ink); background: var(--section-bg); position: relative; }

  .site-header { position: absolute; top: 0; left: 0; width: 1200px; height: 53px; background: var(--header-bg); border-bottom: 4px solid var(--rule); }
  .brand { position: absolute; left: 185px; top: 0; width: 157px; height: 49px; background: var(--green); display: flex; align-items: center; justify-content: center; font-size: 26px; font-weight: 700; letter-spacing: 3px; color: var(--ink); }
  .main-nav { position: absolute; left: 395px; top: 19px; display: flex; align-items: center; }
  .main-nav a { font-size: 12px; font-weight: 700; color: var(--ink); text-decoration: none; padding: 0 11px; line-height: 14px; border-left: 1px solid #555; }
  .main-nav a:first-child { border-left: none; }
  .main-nav a.is-current { color: var(--green-dark); }
  .main-nav a.gap-wide { padding-right: 18px; }
  .main-nav a.gap-wide + a { padding-left: 18px; }

  .hero { position: absolute; top: 53px; left: 0; width: 1200px; height: 224px; }
  .hero-art { position: absolute; inset: 0; background: radial-gradient(ellipse at 55% 85%, #1a1a1a 0%, #3b3b3b 30%, #6d6d6d 60%, #2a2a2a 100%); }
  .hero-title { position: absolute; top: 44px; width: 100%; text-align: center; font-size: 40px; font-weight: 400; color: var(--white); text-shadow: 0 3px 6px rgba(0,0,0,.6); letter-spacing: .5px; }

  .features { position: absolute; top: 277px; left: 0; width: 1200px; height: 325px; }
  .feature { position: absolute; top: 42px; width: 170px; text-align: center; }
  .feature svg { display: block; margin: 0 auto; width: 80px; height: 80px; }
  .feature p { margin-top: 36px; font-size: 12px; line-height: 15.4px; color: var(--ink); }
  .f1 { left: 194px; } .f2 { left: 406px; } .f3 { left: 617px; } .f4 { left: 823px; }

  .site-footer { position: absolute; top: 602px; left: 0; width: 1200px; height: 49px; background: var(--footer-bg); border-top: 4px solid var(--green); color: var(--white); font-size: 12px; display: flex; align-items: center; justify-content: center; }
</style>
</head>
<body>
  <header class="site-header">
    <div class="brand">KSR</div>
    <nav class="main-nav">
      <a href="#" class="is-current">USER HOME</a>
      <a href="#">ADD A JOB</a>
      <a href="#">CURRENT JOBS</a>
      <a href="#" class="gap-wide">SEARCH JOBS</a>
      <a href="#" class="gap-wide">REPORTS</a>
      <a href="#">USER DETAILS</a>
      <a href="#">ADMIN</a>
    </nav>
  </header>

  <section class="hero">
    <div class="hero-art" role="img" aria-label="Black and white photo of an artist drawing a mural on a wall"></div>
    <h1 class="hero-title">HELPING YOU CLEAN UP YOUR COMMUNITY</h1>
  </section>

  <section class="features">
    <div class="feature f1">
      <svg viewBox="0 0 80 80" aria-hidden="true">
        <circle cx="26" cy="24" r="15" fill="none" stroke="var(--green)" stroke-width="9" stroke-dasharray="5 3.4"/>
        <circle cx="26" cy="24" r="10" fill="var(--green)"/>
        <circle cx="26" cy="24" r="4" fill="var(--section-bg)"/>
        <circle cx="57" cy="40" r="12" fill="none" stroke="var(--ink)" stroke-width="8" stroke-dasharray="4 2.9"/>
        <circle cx="57" cy="40" r="9" fill="var(--ink)"/>
        <circle cx="57" cy="40" r="3.5" fill="var(--section-bg)"/>
        <circle cx="22" cy="60" r="9" fill="none" stroke="var(--ink)" stroke-width="6" stroke-dasharray="3 2.2"/>
        <circle cx="22" cy="60" r="7" fill="var(--ink)"/>
        <circle cx="22" cy="60" r="2.5" fill="var(--section-bg)"/>
      </svg>
      <p>KSR is an Online Database System to Manage Graffiti in your area or Your Properties. KSR allows you to Register, Track, Report and Archive Graffiti Jobs with Photographic Records.</p>
    </div>
    <div class="feature f2">
      <svg viewBox="0 0 80 80" aria-hidden="true">
        <polygon points="22,10 74,14 70,58 18,54" fill="var(--ink)"/>
        <rect x="10" y="18" width="54" height="52" fill="var(--ink)" stroke="var(--section-bg)" stroke-width="2"/>
        <rect x="16" y="24" width="42" height="38" fill="var(--section-bg)"/>
        <line x1="28" y1="43" x2="46" y2="33" stroke="var(--green)" stroke-width="3"/>
        <line x1="28" y1="43" x2="46" y2="53" stroke="var(--green)" stroke-width="3"/>
        <circle cx="28" cy="43" r="5" fill="var(--green)"/>
        <circle cx="46" cy="33" r="5" fill="var(--green)"/>
        <circle cx="46" cy="53" r="5" fill="var(--green)"/>
      </svg>
      <p>KSR records both Estimated and Actual hours and costs for each job, enabling you to track the effectiveness of Anti Graffiti policy.</p>
    </div>
    <div class="feature f3">
      <svg viewBox="0 0 80 80" aria-hidden="true">
        <path d="M12 4 H48 L60 16 V76 H12 Z" fill="none" stroke="var(--ink)" stroke-width="3"/>
        <path d="M48 4 V16 H60" fill="none" stroke="var(--ink)" stroke-width="3"/>
        <g stroke="var(--ink)" stroke-width="3">
          <line x1="20" y1="26" x2="44" y2="26"/><line x1="20" y1="34" x2="48" y2="34"/>
          <line x1="20" y1="42" x2="44" y2="42"/><line x1="20" y1="50" x2="38" y2="50"/>
          <line x1="20" y1="58" x2="32" y2="58"/>
        </g>
        <polygon points="66,20 76,30 46,60 36,50" fill="var(--green)"/>
        <polygon points="36,50 46,60 32,64" fill="var(--green)"/>
      </svg>
      <p>KSR allows sharing of Critical Graffiti Tag and Photographic Data between its subscribers, assisting with tracking down Serial Graffiti Offenders.</p>
    </div>
    <div class="feature f4">
      <svg viewBox="0 0 80 80" aria-hidden="true">
        <g fill="var(--ink)">
          <rect x="8" y="46" width="10" height="28"/><rect x="22" y="40" width="10" height="34"/>
          <rect x="36" y="44" width="10" height="30"/><rect x="50" y="34" width="10" height="40"/>
          <rect x="64" y="28" width="10" height="46"/>
        </g>
        <polyline points="10,32 28,20 42,26 56,14 70,12" fill="none" stroke="var(--green)" stroke-width="3"/>
        <g fill="var(--green)">
          <circle cx="10" cy="32" r="4"/><circle cx="28" cy="20" r="4"/><circle cx="42" cy="26" r="4"/>
          <circle cx="56" cy="14" r="4"/><circle cx="70" cy="12" r="4"/>
        </g>
      </svg>
      <p>KSR has a Statistical and Comparison Reporting Systems to allow its subscribers to graphically report and compare their Graffiti Data.</p>
    </div>
  </section>

  <footer class="site-footer">Copyright 2014 KSR all rights reserved</footer>
</body>
</html>
```